TL - business card

Tallow Partners is an insurance brokerage firm, inovative, proactive, vigorous, which aims to become the leader of the insurance brokers in Anfrica. We should like to get some designs which should be avoided also in Gray / Metallic for the Administration and Orange / Blue for the Managers (ike in the picture sent). The Blue / Green logo is not the correct one, but the source of the file. Please adjust the color accordingly for the business cards. 1 / Orange / Blue 2 / Gray / Metallic We want something classic but which is transmitted strenght, inovation, modernity and most of all, rapidity. We want something start-up like, very punchy and catching eye remaining profesional at the same time. Name: Dorian Whitlock Function: Managing Director Address: N ° 17/18 Rua Veloso - R / C 2B Direita - Bairro Mutamba - Luanda Tel: (+244) 947 582 316 Email: dorian.whitlock@tallow-p.example Website: www.tallow-p. example We want classic in the front and creative, colorfull at the back. The cards will be printed in relief, with very high quality of paper.
Insurance Broker
Colors
Designer to choose colors to be used in the design.

```html
<!DOCTYPE html>
<html lang="en">
<head>
<meta charset="utf-8">
<title>Tallow Partners – Business Card</title>
<link rel="stylesheet" href="https://fonts.googleapis.com/css2?family=Ubuntu:wght@400;500&display=swap">
<style>
  :root {
    --backdrop: #3b3b3d;
    --brand-orange: #f26722;
    --brand-blue: #29a8e0;
    --paper: #ffffff;
    --ink: #3a3a3a;
    --shadow: rgba(0, 0, 0, 0.35);
  }
  * { box-sizing: border-box; margin: 0; padding: 0; }
  html, body {
    width: 1200px;
    height: 1200px;
    overflow: hidden;
    background: var(--backdrop);
    font-family: "Ubuntu", sans-serif;
  }
  .card {
    position: absolute;
    left: 250px;
    width: 700px;
    height: 400px;
    box-shadow: 0 10px 24px var(--shadow);
  }
  /* Back side */
  .card--back {
    top: 170px;
    background: var(--brand-orange);
    border-radius: 80px 0 80px 0;
    display: flex;
    align-items: center;
    justify-content: center;
    gap: 16px;
  }
  .card--back .brand-dot {
    width: 34px; height: 34px;
    border-radius: 50%;
    border: 4px solid var(--paper);
  }
  .card--back .brand-name {
    color: var(--paper);
    font-weight: 500;
    font-size: 34px;
    letter-spacing: 1px;
    text-transform: uppercase;
  }
  /* Front side */
  .card--front {
    top: 630px;
    background: var(--paper);
    border-radius: 0 80px 0 80px;
    color: var(--ink);
  }
  .holder {
    position: absolute;
    left: 44px;
    top: 42px;
  }
  .holder__name {
    font-size: 24px;
    font-weight: 400;
    text-transform: uppercase;
    letter-spacing: 0.5px;
    line-height: 1;
  }
  .holder__first { color: var(--brand-orange); }
  .holder__last { color: var(--brand-blue); }
  .holder__role {
    font-size: 16px;
    margin-top: 4px;
  }
  .brand {
    position: absolute;
    right: 44px;
    top: 120px;
    display: flex;
    align-items: center;
    gap: 14px;
  }
  .brand__dot {
    width: 40px; height: 40px;
    border-radius: 50%;
    background: var(--brand-orange);
  }
  .brand__name {
    color: var(--brand-orange);
    font-size: 32px;
    font-weight: 500;
    text-transform: uppercase;
    letter-spacing: 0.5px;
  }
  .contact {
    position: absolute;
    left: 44px;
    top: 270px;
    list-style: none;
    font-size: 17px;
    line-height: 28px;
  }
  .contact li { display: flex; align-items: center; gap: 8px; }
  .contact svg { width: 17px; height: 17px; fill: var(--brand-orange); flex: none; }
  .address {
    position: absolute;
    right: 44px;
    top: 282px;
    text-align: right;
    font-style: normal;
    font-size: 17px;
    line-height: 26px;
  }
</style>
</head>
<body>
  <section class="card card--back" aria-label="Card back">
    <span class="brand-dot"></span>
    <span class="brand-name">Tallow Partners</span>
  </section>

  <section class="card card--front" aria-label="Card front">
    <header class="holder">
      <h1 class="holder__name"><span class="holder__first">Dorian</span> <span class="holder__last">Whitlock</span></h1>
      <p class="holder__role">Managing Director</p>
    </header>

    <div class="brand">
      <span class="brand__dot"></span>
      <span class="brand__name">Tallow Partners</span>
    </div>

    <ul class="contact">
      <li>
        <svg viewBox="0 0 24 24" aria-hidden="true"><path d="M6.6 10.8a15.2 15.2 0 0 0 6.6 6.6l2.2-2.2a1 1 0 0 1 1-.25 11.4 11.4 0 0 0 3.6.57 1 1 0 0 1 1 1V20a1 1 0 0 1-1 1A17 17 0 0 1 3 4a1 1 0 0 1 1-1h3.5a1 1 0 0 1 1 1c0 1.25.2 2.45.57 3.57a1 1 0 0 1-.25 1z"/></svg>
        (+244) 947 582 316
      </li>
      <li>
        <svg viewBox="0 0 24 24" aria-hidden="true"><path d="M2 5h20v14H2z" opacity="0"/><path d="M2 5h20v2l-10 6L2 7zM2 9l10 6 10-6v10H2z"/></svg>
        dorian.whitlock@tallow-p.example
      </li>
    </ul>

    <address class="address">
      N ° 17/18 Rua Veloso - R / C<br>
      2B Direita<br>
      Bairro Mutamba - Luanda
    </address>
  </section>
</body>
</html>
```